Infoblatt
Zielgruppe
Talentförderung, Personalentwicklung, Beratung von Personalabteilungen
Zielgruppe: Personaler, HR Verantwortliche
Aufgabenstellung
Es geht um einen "One-Pager", der auf einem Kongress ausgelegt werden soll und in Kurzform einen Überblick über unser Unternehmen und unser Angebot informieren soll.
Wir haben Visitenkarten auf Recyclingpapier und möchten das Blatt konsistent auf das gleiche Papier drucken lassen, daher einfarbig schwarz. Format DIN A4 Hoch.
IDEE: Vom Stil wie eine Infografik aufbauen
TYPO: unser LOGO ist BEBAS NEUE und unsere Schrift Helvetica

```html
<!DOCTYPE html>
<html lang="de">
<head>
<meta charset="utf-8">
<title>Werksinn – Infoblatt</title>
<link href="https://fonts.googleapis.com/css2?family=Bebas+Neue&family=Arimo:wght@400;700&display=swap" rel="stylesheet">
<style>
  :root {
    --ink: #111111;
    --stage: #e9e9e9;
    --paper-light: #e6e6e6;
    --paper-mid: #bdbdbd;
    --paper-dark: #8f8f8f;
    --ring-dark: #7a7a7a;
    --ring-mid: #9c9c9c;
    --ring-light: #bfbfbf;
    --photo-core: #8a8a8a;
  }
  * { margin: 0; padding: 0; box-sizing: border-box; }
  html, body { width: 1200px; height: 1200px; overflow: hidden; }
  body { background: var(--stage); position: relative; font-family: "Arimo", Helvetica, Arial, sans-serif; color: var(--ink); }

  .sheet { position: absolute; overflow: hidden; }
  .sheet-front { left: 60px; top: 66px; width: 778px; height: 1104px; }
  .sheet-back { left: 838px; top: 464px; width: 344px; height: 568px; }

  .backdrop { position: absolute; inset: 0; }
  .sheet-front .backdrop {
    background:
      linear-gradient(180deg, rgba(255,255,255,0) 62%, rgba(240,240,240,.9) 80%, var(--paper-light) 100%),
      linear-gradient(90deg, var(--paper-mid) 0%, var(--paper-light) 22%, var(--paper-mid) 45%, var(--paper-light) 68%, var(--paper-mid) 100%);
  }
  .sheet-back .backdrop {
    background:
      linear-gradient(180deg, var(--paper-light) 0%, var(--paper-mid) 50%, var(--paper-light) 75%, #d4d4d4 100%);
  }

  .overlay { position: absolute; inset: 0; }

  .brand { position: absolute; font-family: "Bebas Neue", "Arial Narrow", sans-serif; font-weight: 400; line-height: 1; color: var(--ink); }
  .sheet-front .brand { left: 487px; top: 42px; font-size: 56px; }
  .sheet-back .brand { left: 84px; top: 122px; font-size: 52px; }

  .block { position: absolute; }
  .block-title { font-family: "Bebas Neue", "Arial Narrow", sans-serif; font-weight: 400; font-size: 52px; line-height: .9; }
  .block-sub { font-family: "Bebas Neue", "Arial Narrow", sans-serif; font-weight: 400; font-size: 30px; line-height: 1; margin-top: 6px; }
  .block-text { font-size: 15px; line-height: 19px; }
  .block-text strong { font-weight: 700; }
  .block-text p + p { margin-top: 19px; }

  .credo { left: 35px; top: 114px; }
  .credo .block-text { position: absolute; top: 100px; width: 450px; }
  .mehrwert { left: 38px; top: 326px; }
  .mehrwert .block-text { margin-top: 34px; width: 230px; }
  .mission { left: 276px; top: 742px; }
  .mission .block-text { margin-top: 26px; width: 460px; }

  .contact { position: absolute; right: 18px; top: 500px; text-align: right; font-size: 8.5px; line-height: 11.5px; color: #333; }
  .social-box { position: absolute; left: 182px; top: 534px; width: 16px; height: 16px; background: #555; }
</style>
</head>
<body>

  <section class="sheet sheet-front">
    <div class="backdrop" role="img" aria-label="Unscharfes Schwarzweißfoto: Holzwand im Hintergrund, Flipchartpapier und Marker auf einem Tisch"></div>

    <svg class="overlay" width="778" height="1104" viewBox="0 0 778 1104">
      <g class="donut" transform="translate(528 496)">
        <path fill="var(--ring-dark)" d="M0 -190 A190 190 0 0 1 164.5 95 L112.6 65 A130 130 0 0 0 0 -130 Z"/>
        <path fill="var(--ring-light)" d="M164.5 95 A190 190 0 0 1 -164.5 95 L-112.6 65 A130 130 0 0 0 112.6 65 Z"/>
        <path fill="var(--ring-mid)" d="M-164.5 95 A190 190 0 0 1 0 -190 L0 -130 A130 130 0 0 0 -112.6 65 Z"/>
        <circle r="130" fill="var(--photo-core)" role="img" aria-label="Unscharfes Foto einer Arbeitsgruppe im Gespräch"/>
      </g>
      <g class="leader-lines" stroke="var(--ink)" stroke-width="1.2" fill="none">
        <polyline points="35,197 643,197 643,362"/>
        <line x1="38" y1="417" x2="410" y2="417"/>
        <polyline points="568,649 568,827 276,827"/>
      </g>
    </svg>

    <div class="brand">WERKSINN</div>

    <div class="block credo">
      <h2 class="block-title">Credo</h2>
      <h3 class="block-sub">Woran wir glauben:</h3>
      <div class="block-text">
        <p>Wir glauben, dass sich persönliche und ökonomische Werte ergänzen - mehr noch, dass sie langfristig nicht ohne einander auskommen und dass sich emotionale Bindung als Mehrwert in Zahlen ausdrückt.</p>
      </div>
    </div>

    <div class="block mehrwert">
      <h2 class="block-title">Mehrwert</h2>
      <h3 class="block-sub">Was wir bieten:</h3>
      <div class="block-text">
        <p>Wir beraten Unternehmen im Rahmen der Talentförderung und helfen Jugendlichen auf dem Weg in ihr Berufsleben.</p>
        <p><strong>Für Unternehmen:</strong><br>Talentförderung &amp; Talent Management<br>Professionalisierung der Personalarbeit<br>Organisationsentwicklung<br>Potentialorientierte Mit-<br>arbeiterführung</p>
        <p><strong>Für die junge Generation:</strong><br>Berufsorientierung<br>Bewerbungscoaching</p>
      </div>
    </div>

    <div class="block mission">
      <h2 class="block-title">Mission</h2>
      <h3 class="block-sub">Was unser Handeln leitet:</h3>
      <div class="block-text">
        <p>Kundare heißt marktschreierisch anpreisen, hinters Licht führen, täuschen. Mandare heißt beauftragen, Vertrauen schenken. Wir legen großen Wert auf eine Beziehung, die Mandare, nicht Kundare entspricht. Für uns ist der partnerschaftliche Umgang mit unseren Mandanten das Fundament. Wir haben keine Kunden. Wir unterstützen Mandanten.</p>
      </div>
    </div>
  </section>

  <section class="sheet sheet-back">
    <div class="backdrop" role="img" aria-label="Unscharfes Schwarzweißfoto von Kreidestücken auf einem Tisch"></div>

    <svg class="overlay" width="344" height="568" viewBox="0 0 344 568">
      <g class="donut" transform="translate(220 226)">
        <path fill="var(--ring-dark)" d="M0 -95 A95 95 0 0 1 82.3 47.5 L60.6 35 A70 70 0 0 0 0 -70 Z"/>
        <path fill="var(--ring-light)" d="M82.3 47.5 A95 95 0 0 1 -82.3 47.5 L-60.6 35 A70 70 0 0 0 60.6 35 Z"/>
        <path fill="var(--ring-mid)" d="M-82.3 47.5 A95 95 0 0 1 0 -95 L0 -70 A70 70 0 0 0 -60.6 35 Z"/>
      </g>
      <g class="team" fill="#f2f2f2" stroke="#ffffff" stroke-width="2">
        <circle cx="28" cy="225" r="24" role="img" aria-label="Porträtfoto Teammitglied 1"/>
        <circle cx="80" cy="225" r="24" role="img" aria-label="Porträtfoto Teammitglied 2"/>
        <circle cx="134" cy="225" r="24" role="img" aria-label="Porträtfoto Teammitglied 3"/>
        <circle cx="190" cy="225" r="24" role="img" aria-label="Porträtfoto Teammitglied 4"/>
        <circle cx="247" cy="225" r="24" role="img" aria-label="Porträtfoto Teammitglied 5"/>
      </g>
    </svg>

    <div class="brand">WERKSINN</div>

    <address class="contact">
      Lindenweg 12<br>
      40210 Musterstadt<br>
      Fon: 0202.55501420<br>
      E-Mail: info@werksinn.de<br>
      www.werksinn.de
    </address>
    <div class="social-box" aria-hidden="true"></div>
  </section>

</body>
</html>
```